Velundra Jobs portal

Velundra Jobs is a job portal connecting job seekers and companies offering part time jobs in the Mena region, starting in the UAE. We would like to see designs that use the color blue. We have attached images to give an idea what the website should look like. When a company posts a job the job seekers are not allowed to see which company has posted a job. There should also be a coinvex gateway. On the landing page we want a catching picture that we will send.

Target Market(s)

Students and promotional workers

Logo Text

Velundra Jobs

Coding

Coded - Design and coding required

Number of Pages Required

4 page

Font styles to use
Sans Serif

Colors
33a6d7
0692cd
85cae6

```html
<!DOCTYPE html>
<html lang="en">
<head>
<meta charset="utf-8">
<title>Velundra Jobs – Job offers</title>
<link rel="stylesheet" href="https://fonts.googleapis.com/css2?family=Ubuntu:wght@400;500&display=swap">
<style>
:root{
  --blue:#0692cd;
  --blue-mid:#33a6d7;
  --blue-light:#85cae6;
  --text:#3c3c3c;
  --muted:#9a9a9a;
  --page:#f6f6f6;
  --line:#ececec;
  --white:#ffffff;
}
*{box-sizing:border-box;margin:0;padding:0}
html,body{width:1069px;height:1200px;overflow:hidden}
body{font-family:"Ubuntu",sans-serif;color:var(--text);background:var(--white);position:relative;letter-spacing:-0.2px}
.site-header{position:absolute;left:0;top:0;width:1069px;height:100px;background:var(--white)}
.brand{position:absolute;left:114px;top:36px;display:flex;align-items:center;gap:8px}
.brand-mark{width:22px;height:22px;border-radius:50%;background:var(--blue-mid)}
.brand-name{font-size:17px;font-weight:400;color:var(--blue-mid)}
.main-nav{position:absolute;left:433px;top:45px;display:flex;gap:29px;font-size:13px;font-weight:500;color:#444}
.header-tools{position:absolute;left:810px;top:33px;display:flex;align-items:center}
.tool-icon{width:16px;height:16px;display:block}
.avatar{width:41px;height:41px;border-radius:50%;background:radial-gradient(circle at 50% 40%,#c9a58a,#5b6a4a 75%);margin:0 19px 0 26px}
.search-band{position:absolute;left:0;top:100px;width:1069px;height:208px;background:var(--blue)}
.search-label{position:absolute;left:206px;top:72px;font-size:13px;font-weight:500;color:var(--white)}
.field{position:absolute;top:95px;height:31px;background:var(--white);font-size:10px;color:#aaa;padding:0 7px;line-height:31px}
.field.select::after{content:"";position:absolute;right:9px;top:13px;width:4px;height:4px;border-right:1px solid #555;border-bottom:1px solid #555;transform:rotate(45deg)}
.find-btn{position:absolute;left:755px;top:96px;width:112px;height:29px;background:var(--blue-mid);color:var(--white);font-size:12px;font-weight:500;text-align:center;line-height:29px}
.content{position:absolute;left:0;top:308px;width:1069px;height:802px;background:var(--page)}
.categories{position:absolute;left:114px;top:44px;width:132px;height:709px;background:var(--white);border:1px solid #f0f0f0}
.categories h2{position:absolute;left:5px;top:17px;font-size:14px;font-weight:500;color:var(--blue-mid)}
.category-list{position:absolute;left:9px;top:51px;list-style:none;font-size:10px;color:#555;line-height:22.1px}
.view-all{position:absolute;left:9px;top:673px;width:66px;height:21px;background:var(--blue-mid);color:var(--white);font-size:10px;font-weight:500;line-height:21px;text-align:center}
.offers-head{position:absolute;left:258px;top:44px;width:481px;height:44px;background:var(--blue);color:var(--white)}
.offers-head h2{position:absolute;left:13px;top:14px;font-size:14px;font-weight:400}
.pager{position:absolute;right:17px;top:15px;display:flex;gap:8px}
.pager svg{width:9px;height:11px}
.offers-table{position:absolute;left:258px;top:116px;width:481px}
.row{position:absolute;left:0;width:481px;background:var(--white);border:1px solid #f0f0f0;display:flex}
.row>div{border-right:1px solid var(--line);height:100%;position:relative}
.row>div:last-child{border-right:none}
.c-title{width:201px}.c-date{width:75px}.c-prov{width:90px}.c-apply{width:115px}
.table-head{top:0;height:39px;font-size:11px;font-weight:500;color:var(--blue-mid)}
.table-head>div{display:flex;align-items:center;justify-content:center}
.table-head .c-title{justify-content:flex-start;padding-left:11px}
.job{height:86px}
.job .c-title{padding:28px 0 0 11px}
.job-title{font-size:11px;font-weight:500;color:var(--blue-mid)}
.job-place{font-size:10px;color:#555;margin-top:5px}
.job .c-date,.job .c-prov{display:flex;align-items:center;justify-content:center;font-size:10px;color:#555}
.apply-btn{position:absolute;left:24px;top:33px;width:67px;height:20px;background:var(--blue-mid);color:var(--white);font-size:10px;font-weight:500;text-align:center;line-height:20px}
.ads-label{position:absolute;left:761px;top:60px;font-size:11px;color:#666}
.ad{position:absolute;left:761px;width:192px}
.ad-one{top:100px;height:162px;background:linear-gradient(160deg,#9cc94a,#6ea82a)}
.ad-two{top:281px;height:157px;background:linear-gradient(160deg,#5bb8e6,#2b8fcc)}
.ad-three{top:458px;height:165px;background:linear-gradient(155deg,#a5d11c 50%,#4b5560 50%)}
.site-footer{position:absolute;left:0;top:1110px;width:1069px;height:90px;background:var(--white);font-size:11px;color:#444}
.copyright{position:absolute;left:112px;top:38px}
.footer-nav{position:absolute;right:114px;top:38px}
</style>
</head>
<body>
<header class="site-header">
  <div class="brand"><span class="brand-mark"></span><span class="brand-name">Velundra Jobs</span></div>
  <nav class="main-nav"><span>About Us</span><span>Visa Explanation</span><span>Profile</span><span>Contact Us</span></nav>
  <div class="header-tools">
    <svg class="tool-icon" viewBox="0 0 16 16"><circle cx="6.5" cy="6.5" r="4.3" fill="none" stroke="#0692cd" stroke-width="2"/><line x1="9.8" y1="9.8" x2="14" y2="14" stroke="#0692cd" stroke-width="2.4" stroke-linecap="round"/></svg>
    <svg class="tool-icon" viewBox="0 0 16 16" style="margin-left:21px"><path d="M8 1.5c-2.6 0-4.2 2-4.2 4.5v3.5L2.3 12h11.4l-1.5-2.5V6c0-2.5-1.6-4.5-4.2-4.5z" fill="#0692cd"/><circle cx="8" cy="13.8" r="1.6" fill="#0692cd"/></svg>
    <div class="avatar" role="img" aria-label="User profile photo"></div>
    <svg class="tool-icon" viewBox="0 0 16 16"><path d="M4.6 4.2a5.5 5.5 0 1 0 6.8 0" fill="none" stroke="#0692cd" stroke-width="1.8" stroke-linecap="round"/><line x1="8" y1="1.5" x2="8" y2="7.5" stroke="#0692cd" stroke-width="1.8" stroke-linecap="round"/></svg>
  </div>
</header>

<section class="search-band">
  <div class="search-label">Search</div>
  <div class="field" style="left:204px;width:224px">Types of work offered</div>
  <div class="field select" style="left:431px;width:158px">Location</div>
  <div class="field select" style="left:593px;width:157px">Language</div>
  <div class="find-btn">FIND</div>
</section>

<main class="content">
  <aside class="categories">
    <h2>Categories</h2>
    <ul class="category-list">
      <li>All</li><li>Construction (283)</li><li>Engineering (184)</li><li>Retail (165)</li><li>FMCG (139)</li><li>Real Estate (117)</li><li>IT (108)</li><li>Finance (104)</li><li>Oil &amp; Gas (100)</li><li>Law (99)</li><li>Logistics (98)</li><li>Marketing (98)</li><li>Education (89)</li><li>Healthcare (84)</li><li>Manufacturing (65)</li><li>Hospitality (60)</li><li>Accountancy (53)</li><li>Banking (52)</li><li>HR (51)</li><li>Retail Banking (47)</li><li>Media (42)</li><li>General Trading (40)</li><li>Utilities (37)</li><li>Consulting (34)</li><li>Aviation (33)</li><li>Automotive (30)</li><li>Professional Services (28)</li><li>Government (27)</li>
    </ul>
    <div class="view-all">View All &gt;&gt;</div>
  </aside>

  <div class="offers-head">
    <h2>Job offers</h2>
    <div class="pager">
      <svg viewBox="0 0 9 11"><path d="M6.5 1.5 2.5 5.5l4 4" fill="none" stroke="#fff" stroke-width="1.8"/></svg>
      <svg viewBox="0 0 9 11"><path d="M2.5 1.5l4 4-4 4" fill="none" stroke="#fff" stroke-width="1.8"/></svg>
    </div>
  </div>

  <div class="offers-table">
    <div class="row table-head"><div class="c-title">Job Title</div><div class="c-date">Date</div><div class="c-prov">Providers Name</div><div class="c-apply">Apply</div></div>
    <div class="row job" style="top:50px"><div class="c-title"><div class="job-title">Deputy Area Manager</div><div class="job-place">Dubai , Abu Dhabi</div></div><div class="c-date">29-5-2015</div><div class="c-prov">Teralink Abu Dhabi</div><div class="c-apply"><span class="apply-btn">Apply Now</span></div></div>
    <div class="row job" style="top:150px"><div class="c-title"><div class="job-title">Deputy Area Manager</div><div class="job-place">Dubai , Abu Dhabi</div></div><div class="c-date">29-5-2015</div><div class="c-prov">Teralink Abu Dhabi</div><div class="c-apply"><span class="apply-btn">Apply Now</span></div></div>
    <div class="row job" style="top:250px"><div class="c-title"><div class="job-title">Deputy Area Manager</div><div class="job-place">Dubai , Abu Dhabi</div></div><div class="c-date">29-5-2015</div><div class="c-prov">Teralink Abu Dhabi</div><div class="c-apply"><span class="apply-btn">Apply Now</span></div></div>
    <div class="row job" style="top:350px"><div class="c-title"><div class="job-title">Deputy Area Manager</div><div class="job-place">Dubai , Abu Dhabi</div></div><div class="c-date">29-5-2015</div><div class="c-prov">Teralink Abu Dhabi</div><div class="c-apply"><span class="apply-btn">Apply Now</span></div></div>
    <div class="row job" style="top:450px"><div class="c-title"><div class="job-title">Deputy Area Manager</div><div class="job-place">Dubai , Abu Dhabi</div></div><div class="c-date">29-5-2015</div><div class="c-prov">Teralink Abu Dhabi</div><div class="c-apply"><span class="apply-btn">Apply Now</span></div></div>
    <div class="row job" style="top:550px"><div class="c-title"><div class="job-title">Deputy Area Manager</div><div class="job-place">Dubai , Abu Dhabi</div></div><div class="c-date">29-5-2015</div><div class="c-prov">Teralink Abu Dhabi</div><div class="c-apply"><span class="apply-btn">Apply Now</span></div></div>
  </div>

  <div class="ads-label">Advertisements</div>
  <div class="ad ad-one" role="img" aria-label="Advertisement banner for a mobile game"></div>
  <div class="ad ad-two" role="img" aria-label="Advertisement banner for a video game bundle"></div>
  <div class="ad ad-three" role="img" aria-label="Advertisement banner for an online advertising agency"></div>
</main>

<footer class="site-footer">
  <div class="copyright">© 2015 Company Name,&nbsp; All Rights Reserved</div>
  <div class="footer-nav">Home &nbsp;|&nbsp; About Us |Terms &amp; Conditions&nbsp;|&nbsp; FAQ’s</div>
</footer>
</body>
</html>
```